High-end executive coaching group needs a 2 page digital flyer

We need a 2 page digital flyer for a high end leadership coaching offering for global leaders in healthcare. The flyer will advertise a new service (an elite senior leadership coaching group) for senior leaders in the healthcare industry from around the world.
The flyer should be upmarket, professional and minimalist in style to meet the expectations of my professional market (very senior doctors and executives).
The design should be based on my existing logo and brand, see my landing page: www.marlowadvisory.com
The key elements needed are
1) An editable PDF which we can update as we revise the specific details of the offering. The text and draft design for this is attached.
2) The banner image should be high quality but abstract. It can be based on the landing page of my website (the two ripple effects) but does not need to strictly adhere to this.
3) The logo placement of the Marlow Advisory delta sign should be discreet so that it does not dominate
4) The small logos of our professional accrediting organisations should be discreetly placed at the end and should not dominate. They might work best as mono icons in a footer (e.g. blue on a white background, or white on blue.
5) Please find enclosed a previous flyer as an example of a similar style we have used for more junior professionals. The design worked quite well, although we now need a more upmarket version for our senior executives.

Please note this design specifically needs to use existing branding and images from my website: marlowadvisory.com. We are definitely not looking for stock "leadership team" images for this high-end brochure.

Target Market(s)

Senior global leaders in the healthcare industry

Industry/Entity Type

Leading business schools & Healthcare industry.

Font styles to use
Other font styles liked:
• Operetta (selective use for heading) and Sofia Pro (body text)

Colors
0054AA
0677BA
7BADD7
CADEEF
E8F1F8

Requirements
Must have
• Clean minimalist and high professionally look that directly speaks to the interests and perspectives of senior leader leaders in healthcare. It also needs very clear call to action sections
Nice to have
• Effective presentation of the two bios and photographs. These need to look impressive, but should not dominate.
Should not have
• Loud and bold colours, large use of logos.

```html
<!DOCTYPE html>
<html lang="en">
<head>
<meta charset="utf-8">
<title>Marlow Advisory – Analytic Coaching Group flyer</title>
<link href="https://fonts.googleapis.com/css2?family=Figtree:ital,wght@0,400;0,500;0,600;0,700;1,400;1,500&family=Playfair+Display:wght@400;500;600&display=swap" rel="stylesheet">
<style>
:root{
  --brand:#0054AA;
  --brand-mid:#0677BA;
  --brand-soft:#7BADD7;
  --brand-pale:#CADEEF;
  --brand-mist:#E8F1F8;
  --ink:#1d2430;
  --logo-ink:#3b4f84;
  --backdrop:#b3afaf;
  --white:#ffffff;
}
*{margin:0;padding:0;box-sizing:border-box}
html,body{width:1200px;height:900px;overflow:hidden}
body{background:var(--backdrop);font-family:'Figtree',sans-serif;color:var(--ink);position:relative}
.page{position:absolute;top:78px;width:524px;height:744px;background:var(--white);overflow:hidden}
.page--front{left:54px}
.page--back{left:622px}
.abs{position:absolute}
.serif{font-family:'Playfair Display',serif;color:var(--brand);font-weight:500}

/* front */
.hero{left:0;top:0;width:524px;height:177px;background:
  radial-gradient(ellipse 170px 60px at 330px 100px,#c9d5e6 0%,#e3e9f2 45%,transparent 75%),
  linear-gradient(120deg,#dfe6f1 0%,#f2f5f9 40%,#d6dfec 100%)}
.brand-name{left:432px;top:28px;font-family:'Playfair Display',serif;font-size:17px;line-height:16px;color:var(--logo-ink);font-weight:400}
.hero-title{left:41px;top:58px;font-size:35.5px;line-height:43px;font-weight:600}
.band{left:0;top:177px;width:524px;height:61px;background:var(--brand);color:var(--white);font-weight:600;font-size:13.3px;line-height:18px;padding:12px 0 0 45px}
.section-title{left:45px;top:256px;font-size:19.6px;letter-spacing:.3px;white-space:nowrap}
.lead{left:45px;top:294px;width:450px;font-size:11.3px;line-height:13.5px;color:var(--brand-soft);font-weight:600;white-space:nowrap}
.intro{left:45px;top:327px;width:440px;font-size:11.5px;line-height:13.5px}
.benefits{left:32px;top:393px;width:315px;height:175px;border:1.5px solid var(--brand);border-radius:14px}
.benefits-title{left:45px;top:380px;font-size:20px;background:var(--white);padding:0 6px 0 3px}
.benefit-list{left:47px;top:412px;width:290px;list-style:none;font-size:10.2px;line-height:12.6px}
.benefit-list li{position:relative;padding-left:15px;margin-bottom:2px}
.benefit-list svg{position:absolute;left:0;top:2px}
.benefit-list b{color:var(--brand);font-weight:600}
.quote{left:373px;top:403px;width:110px;font-style:italic;font-size:9.9px;line-height:12px;color:var(--brand)}
.quote-mark{font-family:'Playfair Display',serif;font-style:normal;font-weight:600;color:var(--brand-soft);font-size:28px;line-height:0;vertical-align:-9px}
.quote-mark--open{position:absolute;left:-14px;top:14px;vertical-align:0}
.attribution{font-size:8.6px;font-weight:600;color:var(--ink)}
.details-panel{left:140px;top:589px;width:384px;height:155px;background:var(--brand-mist);border-top-left-radius:18px}
.secure{left:44px;top:604px;width:80px;font-size:13.4px;line-height:16.5px;color:var(--brand);font-weight:600}
.label{font-size:11.4px;font-weight:600;color:var(--brand);letter-spacing:.2px}
.value{font-size:11.6px;line-height:15px;color:var(--ink)}
.rule{height:1.2px;background:var(--brand-soft)}
.small-note{font-size:8.3px;font-style:italic;color:var(--brand-mid)}

/* back */
.back-title{left:46px;top:48px;width:440px;font-size:20px;line-height:22.5px}
.portrait{left:46px;width:106px;border-radius:10px}
.portrait--one{top:118px;height:124px;background:linear-gradient(160deg,#6d8f55 0%,#8aa66e 40%,#2f4f86 100%)}
.portrait--two{top:257px;height:112px;background:linear-gradient(160deg,#1a1614 0%,#3a2a24 55%,#d9a894 100%)}
.bio{left:168px;width:302px;font-size:10px;line-height:12.05px}
.bio b{color:var(--brand);font-weight:600}
.questions{left:46px;top:405px;width:434px;height:99px;border:1.5px solid var(--brand);border-radius:14px}
.questions-title{left:60px;top:397px;font-size:13.8px;line-height:16.3px;background:var(--white);padding:0 6px 0 5px;white-space:nowrap}
.question-list{left:65px;top:436px;list-style:none;font-size:10.8px;line-height:17.6px;font-weight:500;white-space:nowrap}
.question-list li{position:relative;padding-left:15px}
.question-list svg{position:absolute;left:0;top:5px}
.cta-panel{left:233px;top:529px;width:291px;height:179px;background:var(--brand-mist);border-top-left-radius:18px}
.quote-two{left:63px;top:540px;width:162px;font-style:italic;font-size:11.4px;line-height:13.5px;color:var(--brand)}
.cta-head{font-size:12.2px;font-weight:700;color:var(--brand);letter-spacing:.2px}
.cta-body{font-size:12.6px;line-height:19px;font-weight:600;color:var(--ink);white-space:nowrap}
.footer{left:0;top:708px;width:524px;height:36px;background:var(--brand)}
.footer-url{left:46px;top:11px;color:var(--white);font-size:10.8px;font-weight:600}
.badge{top:13px;height:11px;background:rgba(255,255,255,.85)}
</style>
</head>
<body>

<section class="page page--front">
  <div class="abs hero" role="img" aria-label="Abstract soft-blue water surface with concentric ripples"></div>
  <div class="abs brand-name">Marlow<br>Advisory</div>
  <h1 class="abs hero-title serif">Elevate and Ignite<br>Your Leadership</h1>
  <div class="abs band">Transformative conversations for senior healthcare leaders. Unlock<br>purpose, engage authentically and amplify your leadership impact.</div>

  <h2 class="abs section-title serif">Analytic Coaching Group for Senior Leaders</h2>
  <p class="abs lead">As a senior leader in healthcare, you’re constantly navigating challenges.<br>But where do you turn for authentic connections, reflection and personal growth?</p>
  <p class="abs intro">Rethink your leadership assumptions and approach challenges with fresh creativity. Secure your spot in our exclusive Analytic Coaching Group and ignite your leadership potential.</p>

  <div class="abs benefits"></div>
  <h3 class="abs benefits-title serif">Benefits to you</h3>
  <ul class="abs benefit-list">
    <li><svg width="9" height="8" viewBox="0 0 9 8"><path d="M1 4.2l2.3 2.3L8 1.3" fill="none" stroke="#7BADD7" stroke-width="1.6"/></svg><b>Transformative conversations:</b><br>Engage in discussions that spark innovative leadership</li>
    <li><svg width="9" height="8" viewBox="0 0 9 8"><path d="M1 4.2l2.3 2.3L8 1.3" fill="none" stroke="#7BADD7" stroke-width="1.6"/></svg><b>Peer insights:</b> Harness fresh insights from peers, enhancing<br>your decision-making and effectiveness</li>
    <li><svg width="9" height="8" viewBox="0 0 9 8"><path d="M1 4.2l2.3 2.3L8 1.3" fill="none" stroke="#7BADD7" stroke-width="1.6"/></svg><b>Reimagined leadership:</b> Channel your creativity and<br>redefine your leadership, personally and professionally</li>
    <li><svg width="9" height="8" viewBox="0 0 9 8"><path d="M1 4.2l2.3 2.3L8 1.3" fill="none" stroke="#7BADD7" stroke-width="1.6"/></svg><b>Instant 360° insights:</b> Gain real-time feedback from trusted<br>peers to enrich your leadership</li>
    <li><svg width="9" height="8" viewBox="0 0 9 8"><path d="M1 4.2l2.3 2.3L8 1.3" fill="none" stroke="#7BADD7" stroke-width="1.6"/></svg><b>Lead authentically:</b> Develop effective strategies using the<br>latest insights from group and leadership psychology</li>
  </ul>

  <blockquote class="abs quote">
    <span class="quote-mark quote-mark--open">“</span>You bare your heart and share things you wouldn’t under normal circumstances.<br>You get to know each other very quickly. There’s that sort of intense, shared experience that comes from speaking to each other’s lives. <span class="quote-mark">”</span>
  </blockquote>
  <p class="abs attribution" style="left:372px;top:548px">Sarah, Medical Director</p>

  <div class="abs details-panel"></div>
  <p class="abs secure">Secure your spot now and ignite your leadership potential..</p>
  <div class="abs" style="left:158px;top:604px;width:104px">
    <p class="label">DATES:</p>
    <p class="value">7 February 2024 –<br>11 December 2024</p>
    <div class="rule" style="margin:9px 0 10px"></div>
    <p class="label">TIME:</p>
    <p class="value">7:30am – 8:45am<br>(UK time)</p>
  </div>
  <div class="abs" style="left:274px;top:603px;width:245px">
    <p class="label">COMMITMENT:</p>
    <p class="value">Wednesdays, every 2 weeks</p>
    <p class="label" style="margin-top:5px">LOCATION:</p>
    <p class="value">Connect from anywhere by secure video call</p>
    <p class="label" style="margin-top:5px">COST:</p>
    <p class="value">£3350 (UK) <span style="color:var(--brand)">|</span> €3900 (EU) <span style="color:var(--brand)">|</span> A$6530 (AU)</p>
    <p class="small-note">Payment options available</p>
  </div>
</section>

<section class="page page--back">
  <h2 class="abs back-title serif">Expertly guided by insight, academic rigour and practical leadership strategies</h2>

  <div class="abs portrait portrait--one" role="img" aria-label="Portrait photograph of Professor Daniel Marlow"></div>
  <p class="abs bio" style="top:119px"><b>Professor Daniel Marlow</b> has 30 years’ experience developing leaders. An award-winning business school professor, group analyst and psychoanalytic psychotherapist, he has taught senior leadership programmes at Ashbury University, Kingsbridge College and Southgate University. His extensive leadership experience as a public health service clinical director and consultant psychotherapist inform his work as an internationally accredited executive coach. With a PhD from Westbrook University, he is an expert in melding psychological insights with strategic organisational change.</p>

  <div class="abs portrait portrait--two" role="img" aria-label="Portrait photograph of Dr Helen Ashford"></div>
  <p class="abs bio" style="top:258px"><b>Dr Helen Ashford</b> is a renowned psychoanalyst, group analyst, consultant psychiatrist and organisational consultant in the health sector. She has 20 years of leadership within the public health service, and she was also the National Director of Therapies for the Harbour Care Group, directing therapy services across 100 UK hospitals. She holds prominent positions as Chair of the Patient Safety Group, Chair of the Working Group on the Effect of Suicide and Homicide on Psychiatrists, and Vice Chair of the Psychotherapy Faculty at the Royal Society of Psychiatric Practice.</p>

  <div class="abs questions"></div>
  <h3 class="abs questions-title serif">Engage with global leaders, gain diverse insights and forge<br>lasting bonds. Explore questions such as:</h3>
  <ul class="abs question-list">
    <li><svg width="9" height="8" viewBox="0 0 9 8"><path d="M1 4.2l2.3 2.3L8 1.3" fill="none" stroke="#0054AA" stroke-width="1.6"/></svg>What kind of leader do I aspire to be in the next chapter of my life and career?</li>
    <li><svg width="9" height="8" viewBox="0 0 9 8"><path d="M1 4.2l2.3 2.3L8 1.3" fill="none" stroke="#0054AA" stroke-width="1.6"/></svg>What unique qualities and actions do I offer that no one else can?</li>
    <li><svg width="9" height="8" viewBox="0 0 9 8"><path d="M1 4.2l2.3 2.3L8 1.3" fill="none" stroke="#0054AA" stroke-width="1.6"/></svg>How can I galvanise my personal strengths to inspire and motivate others?</li>
  </ul>

  <blockquote class="abs quote-two">
    <span class="quote-mark quote-mark--open" style="left:-19px">“</span>Through this exceptional coaching, our leadership team elevated its performance to lead the hospital with greater clarity, cohesion and thoughtfulness. Not only do we provide a superior work environment for staff, but better care for our patients. <span class="quote-mark">”</span>
  </blockquote>
  <p class="abs attribution" style="left:62px;top:669px">John, CEO</p>

  <div class="abs cta-panel"></div>
  <p class="abs cta-head" style="left:258px;top:545px">BOOK YOUR FREE DISCOVERY CALL</p>
  <p class="abs cta-body" style="left:258px;top:562px">daniel@marlowadvisory.com<br>helenashford@mail.com</p>
  <div class="abs rule" style="left:258px;top:611px;width:218px"></div>
  <p class="abs cta-head" style="left:258px;top:627px">LIMITED SPOTS AVAILABLE</p>
  <p class="abs cta-body" style="left:258px;top:644px">Don’t miss this unique opportunity to<br>transform your leadership journey.</p>

  <footer class="abs footer">
    <span class="abs footer-url">www.marlowadvisory.com</span>
    <span class="abs badge" style="left:299px;top:10px;width:16px;height:16px;border-radius:50%"></span>
    <span class="abs badge" style="left:335px;width:34px;border-radius:2px"></span>
    <span class="abs badge" style="left:386px;width:30px;border-radius:2px"></span>
    <span class="abs badge" style="left:433px;width:46px;border-radius:2px"></span>
  </footer>
</section>

</body>
</html>
```